Luxury travel agency needs a website design

We are a travel agency specializing in booking luxury vacations. We specialize in Hawaii, Europe and Caribbean, but will do all vacations. I want a very classy website design which would attract luxury clients. The company name is "Harbors and Hammocks Travel Agency". Would love the web design to go with the color scheme of the logo. Hex codes included in files. Logo is attached. Would also love more Grey in the website. I want it very elegant

Coding

Coded - Design and coding required

Font styles to use
Sans Serif
Decorative

Requirements
Must have
• - Consultation Tab or a page where the client can fill out a short form about what vacation that they would want to book. I want this info to be sent to me in order for me to contact them.
- Somewhere with my contact info "email: marla@harborsandhammockstravel.example and phone number"
- Social media links
- About section "Marla Dunbevy - Agency Owner (picture provided)
Marla has been traveling full time for the passed two years and has been very passionate about travel from a young age. Marla is dedicated to working closely with clients to book their dream vacation.
Marla's specializations include honeymoons and anniversaries focusing on travel in Europe, Hawaii and all inclusive resorts in the Caribbean.

```html
<!DOCTYPE html>
<html lang="en">
<head>
<meta charset="utf-8">
<title>Harbors and Hammocks Travel Agency</title>
<link href="https://fonts.googleapis.com/css2?family=Cinzel:wght@600;700&family=Roboto:ital,wght@0,400;0,500;0,700;1,400&display=swap" rel="stylesheet">
<style>
:root{
  --yellow:#f5c060;
  --orange:#ef8c55;
  --orange-soft:#e9a57a;
  --ink:#1b1b1b;
  --grey-text:#6f6f6f;
  --grey-light:#f2f2f2;
  --footer:#4a4a4a;
  --white:#ffffff;
}
*{box-sizing:border-box;margin:0;padding:0}
html,body{width:1200px;height:3919px;overflow:hidden}
body{position:relative;font-family:"Roboto",Arial,sans-serif;color:var(--ink);background:var(--white)}
.abs{position:absolute}
.display{font-family:"Cinzel",Georgia,serif;font-weight:700;letter-spacing:1px}
.btn{position:absolute;display:flex;align-items:center;justify-content:center;gap:8px;border-radius:30px;color:var(--white);font-weight:700;font-size:14px;text-transform:uppercase;letter-spacing:.3px;white-space:nowrap}
.btn .dot{width:13px;height:13px;border-radius:50%;background:var(--white);position:relative}
.btn .dot::after{content:"";position:absolute;left:4px;top:3.5px;border-left:5px solid var(--orange);border-top:3px solid transparent;border-bottom:3px solid transparent}
.btn.yellow{background:var(--yellow)}
.btn.orange{background:var(--orange)}
.btn.yellow .dot::after{border-left-color:var(--yellow)}

/* top bar */
.topbar{top:0;left:0;width:1200px;height:43px;background:var(--yellow);color:var(--white);font-size:14px}
.topbar .mail{left:113px;top:13px;display:flex;gap:14px;align-items:center}
.topbar .phone{left:803px;top:11px;font-size:16px;font-weight:500;display:flex;gap:16px;align-items:center}
.topbar .social{left:993px;top:15px;display:flex;gap:10px}
.social span{width:13px;height:13px;border-radius:50%;background:var(--white);display:block}

/* nav */
.nav{top:43px;left:0;width:1200px;height:76px;background:var(--white)}
.brand{left:114px;top:20px;display:flex;align-items:center;gap:8px;font-size:15px;font-weight:700;color:var(--ink)}
.brand .mark{width:28px;height:28px;border-radius:50%;background:var(--yellow)}
.menu{left:483px;top:32px;display:flex;gap:18px;font-size:14px;font-weight:700;text-transform:uppercase}
.menu .active{color:var(--orange)}
.nav .btn{left:938px;top:22px;width:151px;height:37px;font-size:14px}

/* hero */
.hero{top:119px;left:0;width:1200px;height:600px;background:linear-gradient(100deg,#4f86c6 0%,#8fb9e3 30%,#dfe7ee 55%,#d9a0a4 68%,#c9d2dc 82%,#a8b7c8 100%)}
.hero .welcome{left:113px;top:170px;color:var(--white);font-size:24px}
.hero h1{position:absolute;left:113px;top:212px;color:var(--white);font-size:43px;line-height:53px}

/* search */
.search{top:627px;left:111px;width:978px;height:187px;background:var(--white);box-shadow:0 2px 12px rgba(0,0,0,.12)}
.search h2{position:absolute;left:29px;top:40px;font-size:19px}
.field{position:absolute;top:98px;width:179px;height:51px;border:1px solid #e2e2e2;font-size:12px;color:var(--grey-text);padding:18px 13px;display:flex;justify-content:space-between}
.field i{width:8px;height:8px;background:#777;border-radius:2px;display:block;margin-top:3px}
.search .btn{left:772px;top:98px;width:179px;height:51px;border-radius:0;background:var(--orange)}

/* about */
.about-bg{top:1030px;left:115px;width:1085px;height:420px;background:linear-gradient(transparent,#f7f7f7)}
.portrait{left:135px;top:913px;width:426px;height:426px;border-radius:50%;background:linear-gradient(160deg,var(--orange),var(--yellow));padding:8px}
.portrait div{width:100%;height:100%;border-radius:50%;background:linear-gradient(160deg,#8a7a6a,#b9a08d 50%,#5ea4c4);border:4px solid var(--white)}
.about h2{position:absolute;left:666px;top:963px;font-size:37px}
.about p{position:absolute;left:666px;top:1025px;width:430px;font-size:15.5px;line-height:30px;color:var(--grey-text)}
.about .btn{left:666px;top:1262px;width:172px;height:48px}

/* confidence panels */
.panel{top:1480px;width:600px;height:455px;text-align:center;color:var(--white)}
.panel.left{left:0;background:linear-gradient(#f4c468,#f0bf62)}
.panel.right{left:600px;background:linear-gradient(#e98f5a,#ec9a66)}
.panel h2{position:absolute;top:84px;left:0;width:600px;font-size:26px}
.panel p{position:absolute;top:130px;left:55px;width:490px;font-size:14.5px;line-height:27.5px}
.panel .btn{left:223px;top:316px;width:154px;height:47px}

/* tours */
.tours-title{top:2032px;left:0;width:1200px;text-align:center;font-size:37px}
.tour{top:2135px;width:245px;height:303px}
.t1{left:111px;background:linear-gradient(#8bb6e0,#3d6a4c 60%,#2ea6a8)}
.t2{left:356px;background:var(--orange-soft);color:var(--white);text-align:center}
.t3{left:600px;background:linear-gradient(#9cc3e7,#6e8e5c 60%,#e0a93c)}
.t4{left:845px;background:linear-gradient(#a8c9ea,#7f8fa0 45%,#3aa6c4 75%,#9a8c7a)}
.t2 h3{position:absolute;top:56px;left:0;width:245px;font-size:17px;line-height:22px}
.t2 p{position:absolute;top:114px;left:18px;width:209px;font-size:13.5px;line-height:22px}
.t2 .btn{left:53px;top:200px;width:139px;height:40px;font-size:13px}

/* banner */
.banner{top:2569px;left:0;width:1200px;height:371px;background:linear-gradient(90deg,#c98a5a 0%,#e9a56f 25%,#9fd0d6 55%,#6cc0cf 100%)}
.banner h2{position:absolute;top:72px;left:400px;width:640px;text-align:center;color:var(--white);font-size:38px;line-height:43px}
.banner .sub{position:absolute;top:186px;left:400px;width:640px;text-align:center;color:var(--white);font-size:18px;font-weight:700}
.banner .btn{left:616px;top:242px;width:216px;height:47px;font-size:13px}

/* testimonials */
.skyline{top:3300px;left:0;width:1200px;height:241px;background:linear-gradient(transparent,#ededed)}
.say-title{top:3033px;left:0;width:1200px;text-align:center;font-size:30px}
.card{top:3130px;width:318px;height:239px;background:var(--white);box-shadow:0 1px 8px rgba(0,0,0,.1);padding:22px 14px}
.card .quote{color:var(--orange);font-family:Georgia,serif;font-size:44px;font-weight:700;line-height:30px}
.card p{margin-top:14px;font-size:13px;line-height:23px;font-style:italic;color:var(--grey-text)}
.card .who{position:absolute;left:14px;top:178px;display:flex;gap:26px;align-items:center}
.card .avatar{width:52px;height:52px;border-radius:50%;background:linear-gradient(#c9d3de,#5b6b80)}
.card .name{color:var(--orange);font-weight:700;font-size:13.5px}
.card .role{color:#555;font-size:13.5px;margin-top:4px}
.dots{top:3428px;left:572px;display:flex;gap:3px}
.dots span{width:9px;height:9px;border-radius:50%;background:var(--orange)}
.dots span.off{background:transparent;border:2px solid var(--orange)}

/* footer */
.footer{top:3541px;left:0;width:1200px;height:378px;background:var(--footer);color:var(--white)}
.footer h4{font-size:14.5px;font-weight:700;text-decoration:underline;text-transform:uppercase;margin-bottom:14px}
.col{position:absolute;top:68px;font-size:15px}
.col li{list-style:none;height:34px;display:flex;gap:14px}
.col li::before{content:"»";font-weight:700}
.contact{width:250px}
.contact-row{display:flex;gap:18px;align-items:center;height:58px;font-size:13.5px;line-height:21px;white-space:nowrap}
.contact-row .ic{width:30px;height:30px;border-radius:50%;background:var(--white);flex:none;position:relative}
.contact-row .ic::after{content:"";position:absolute;left:10px;top:10px;width:10px;height:10px;border-radius:50%;background:var(--yellow)}
.news p{font-size:15px;line-height:25px;width:280px}
.news .input{margin-top:14px;width:272px;height:48px;background:var(--white);color:#777;font-size:13.5px;padding:15px 20px}
.news .btn{position:relative;margin-top:14px;width:147px;height:48px}
.footer .rule{position:absolute;left:111px;top:307px;width:1078px;height:1px;background:#6a6a6a}
.footer .copy{position:absolute;left:111px;top:328px;font-size:14px}
.footer .social{position:absolute;left:980px;top:329px;display:flex;gap:14px}
.footer .social span{width:15px;height:15px}
.footer .code{position:absolute;left:1152px;top:331px;font-size:11px}
</style>
</head>
<body>

<header class="abs topbar">
  <div class="abs mail">
    <svg width="14" height="11" viewBox="0 0 14 11"><rect x="0.5" y="0.5" width="13" height="10" fill="none" stroke="#fff"/><path d="M1 1l6 5 6-5" fill="none" stroke="#fff"/></svg>
    info@hhtravel.example
  </div>
  <div class="abs phone">
    <svg width="14" height="14" viewBox="0 0 14 14"><path d="M3 1l2 3-1.5 1.5c1 2 2.5 3.5 4.5 4.5L9.5 8.5l3 2-1.5 2.5C6 13 1 8 1 2.5z" fill="#fff"/></svg>
    1 800 555 0142
  </div>
  <div class="abs social"><span></span><span></span><span></span><span></span></div>
</header>

<nav class="abs nav">
  <div class="abs brand"><span class="mark"></span>Harbors &amp; Hammocks</div>
  <div class="abs menu">
    <span class="active">Home</span><span>About Us</span><span>Destination</span><span>Custom</span><span>Contact Us</span>
  </div>
  <div class="btn orange">Consultation</div>
</nav>

<section class="abs hero" role="img" aria-label="Traveller in a red dress with a sun hat above whitewashed village with blue domes and the sea">
  <div class="abs welcome display">Welcome to</div>
  <h1 class="display">Harbors &amp; Hammocks<br>Travel Agency.</h1>
</section>

<section class="abs search">
  <h2 class="display">Where do you want to go?</h2>
  <div class="field" style="left:27px">Destination<i></i></div>
  <div class="field" style="left:213px">Any Tour Type<i></i></div>
  <div class="field" style="left:399px">All Months<i></i></div>
  <div class="field" style="left:585px">Travelers<i></i></div>
  <div class="btn">Search
    <svg width="13" height="13" viewBox="0 0 13 13"><circle cx="5.5" cy="5.5" r="4" fill="none" stroke="#fff" stroke-width="2"/><path d="M8.5 8.5l3.5 3.5" stroke="#fff" stroke-width="2"/></svg>
  </div>
</section>

<section class="about">
  <div class="abs about-bg" role="img" aria-label="Faint line drawing of travel landmarks behind the about section"></div>
  <div class="abs portrait" role="img" aria-label="Portrait photo of Marla Dunbevy, agency owner"><div></div></div>
  <h2 class="display">About Me</h2>
  <p>Marla has been traveling full time for the passed two years and has been very passionate about travel from a young age. Marla is dedicated to working closely with clients to book their dream vacation.<br>Marla's specializations include honeymoons &amp; anniversaries focusing on travel in Europe, Hawaii and all inclusive resorts in the Caribbean.</p>
  <div class="btn orange">Learn More <span class="dot"></span></div>
</section>

<section class="abs panel left" role="img" aria-label="Yellow-tinted photo of travellers with suitcases by a mountain lake">
  <h2 class="display">Book with Confidence</h2>
  <p>Lorem ipsum dolor sit amet, consectetur adipiscing elit, sed do eiusmod tempor incididunt ut labore et dolore magna aliqua. Ut enim ad minim veniam, quis nostrud exercitation ullamco laboris nisi ut aliquip ex ea commodo consequat. Duis aute irure dolor in reprehenderit in voluptate velit esse cillum dolore eu fugiat nulla pariatur. Excepteur sint occaecat cupidatat non proident, sunt in culpa</p>
  <div class="btn orange">Learn More <span class="dot"></span></div>
</section>
<section class="abs panel right" role="img" aria-label="Orange-tinted photo of mountains and forest">
  <h2 class="display">Travel with Confidence</h2>
  <p>Lorem ipsum dolor sit amet, consectetur adipiscing elit, sed do eiusmod tempor incididunt ut labore et dolore magna aliqua. Ut enim ad minim veniam, quis nostrud exercitation ullamco laboris nisi ut aliquip ex ea commodo consequat. Duis aute irure dolor in reprehenderit in voluptate velit esse cillum dolore eu fugiat nulla pariatur. Excepteur sint occaecat cupidatat non proident, sunt in culpa</p>
  <div class="btn yellow">Learn More <span class="dot"></span></div>
</section>

<h2 class="abs tours-title display">Summer 2021 Tours</h2>
<div class="abs tour t1" role="img" aria-label="Hiker resting above a turquoise mountain lake"></div>
<div class="abs tour t2">
  <h3 class="display">Lorem Ipsum<br>Dolor Sit</h3>
  <p>Sed ut perspiciatis unde om nis iste natus error svoluptatem accusantium dolorelaudan</p>
  <div class="btn yellow">Learn More <span class="dot"></span></div>
</div>
<div class="abs tour t3" role="img" aria-label="Traveller in a yellow jacket overlooking a city"></div>
<div class="abs tour t4" role="img" aria-label="Hiker on a rocky ledge above a glacial lake"></div>

<section class="abs banner" role="img" aria-label="Silhouette of a traveller with a suitcase at an airport window">
  <h2 class="display">The Great Canadian<br>Advantage</h2>
  <div class="sub">STOP DREAMING AND LET US CREATE YOUR BEST DAYS EVER!</div>
  <div class="btn orange">Why Book With Us <span class="dot"></span></div>
</section>

<div class="abs skyline" role="img" aria-label="Faint skyline of world landmarks"></div>
<h2 class="abs say-title display">What Our Customer Says</h2>
<div class="abs card" style="left:111px">
  <div class="quote">&ldquo;</div>
  <p>Lorem ipsum dolor sit ametconsectetuadipiscing elit, sed do eiusmod tempor incididunt ut labore et dolore magna aliqua.</p>
  <div class="who"><div class="avatar" role="img" aria-label="Customer photo"></div><div><div class="name">JULIE RENFORD</div><div class="role">Businessman</div></div></div>
</div>
<div class="abs card" style="left:441px">
  <div class="quote">&ldquo;</div>
  <p>Lorem ipsum dolor sit ametconsectetuadipiscing elit, sed do eiusmod tempor incididunt ut labore et dolore magna aliqua.</p>
  <div class="who"><div class="avatar" role="img" aria-label="Customer photo"></div><div><div class="name">JULIE RENFORD</div><div class="role">Businessman</div></div></div>
</div>
<div class="abs card" style="left:771px">
  <div class="quote">&ldquo;</div>
  <p>Lorem ipsum dolor sit ametconsectetuadipiscing elit, sed do eiusmod tempor incididunt ut labore et dolore magna aliqua.</p>
  <div class="who"><div class="avatar" role="img" aria-label="Customer photo"></div><div><div class="name">JULIE RENFORD</div><div class="role">Businessman</div></div></div>
</div>
<div class="abs dots"><span></span><span></span><span class="off"></span><span></span><span></span></div>

<footer class="abs footer">
  <div class="col" style="left:111px"><h4>Quick Links</h4>
    <ul><li>Home</li><li>About Us</li><li>Destination</li><li>Contact Us</li><li>Reviews</li></ul></div>
  <div class="col" style="left:325px"><h4>Other Links</h4>
    <ul><li>FAQ</li><li>Help Service</li><li>Terms Of Use</li><li>Privacy Policy</li><li>Clients</li></ul></div>
  <div class="col contact" style="left:551px"><h4>Contact Us</h4>
    <div class="contact-row"><span class="ic"></span>412 Harbor Lane<br>United States</div>
    <div class="contact-row"><span class="ic"></span>1 800 555 0142</div>
    <div class="contact-row"><span class="ic"></span>info@hhtravel.example</div>
  </div>
  <div class="col news" style="left:818px"><h4>Newsletter</h4>
    <p>At vero eos et accusamus et iusto odio dignissimos ducimus qui blanditiis.</p>
    <div class="input">Email Address</div>
    <div class="btn orange">Subscribe <span class="dot"></span></div>
  </div>
  <div class="rule"></div>
  <div class="copy">&copy; 2021 Harbors and Hammocks Travel Agency. All Rights Reserved</div>
  <div class="social"><span></span><span></span><span></span><span></span></div>
  <div class="code">C42</div>
</footer>

</body>
</html>
```